Business Card Design

Just looking for a good designs that looks good with our company logo. I'd like it to be simple and to the point. Just including contact information, our logo, and my name somewhere on the card so future clients know who they're contacting, and a couple services offered. The two images I attached are pictures of our logo. I don't care which color they they are, I just attached both images to give a reference of logo colors depending on the color of the card.
Names: Carl Whitby
Phone: 816-555-0147
Email: greenstripeyard@fernmail.test
Services offered:
Mowing
Fertilization
Aeration
Bed & tree maintenance
and more.
Business
Names: Carl Whitby
Phone: 816-555-0147
(no website)

```html
<!DOCTYPE html>
<html lang="en">
<head>
<meta charset="utf-8">
<title>Greenstripe Yard – Business Card</title>
<link rel="stylesheet" href="https://fonts.googleapis.com/css2?family=Open+Sans:wght@400;600;700;800&display=swap">
<style>
  :root{
    --coral:#e8503a;
    --navy:#2e303f;
    --band-grey:#cfd0d2;
    --paper:#f4f4f4;
    --ink:#2b2d3a;
    --rule:#c9cacc;
    --backdrop:#e6e6e4;
  }
  *{box-sizing:border-box;margin:0;padding:0}
  html,body{width:1200px;height:1173px;overflow:hidden}
  body{background:var(--backdrop);font-family:"Open Sans",Arial,sans-serif;color:var(--ink);position:relative}

  .card{position:absolute;top:246px;width:430px;height:680px;box-shadow:0 6px 18px rgba(0,0,0,.18)}
  .card--front{left:120px;background:var(--coral);padding:26px 26px 48px}
  .card--back{left:650px;background:var(--navy);padding:26px 26px 40px}

  .panel{width:100%;height:100%;background:var(--paper);overflow:hidden;display:flex;flex-direction:column}
  .card--front .panel{border-radius:0 54px 0 54px}
  .card--back .panel{border-radius:54px 0 54px 0}

  .top-band{height:118px;flex:none;background:var(--band-grey);display:flex;align-items:center;justify-content:center}
  .services{list-style:none;display:flex;flex-wrap:wrap;justify-content:center;gap:4px 0;padding:0 30px;font-size:16px;line-height:1.35;color:var(--ink);text-align:center}
  .services__item + .services__item::before{content:"·";margin:0 7px}
  .services__item--break{flex-basis:100%;height:0}
  .services__item--break + .services__item::before{content:none}
  .divider{height:5px;flex:none;background:var(--coral)}

  .brand{flex:1;display:flex;align-items:center;justify-content:center;gap:14px;padding-bottom:40px}
  .brand__dot{width:30px;height:30px;border-radius:50%;background:var(--coral);flex:none}
  .brand__name{font-size:34px;font-weight:800;letter-spacing:1px;color:var(--navy);line-height:1.05;text-transform:uppercase}

  .contacts{flex:1;padding:34px 28px 0 34px;display:flex;flex-direction:column;gap:22px}
  .contact{display:flex;align-items:center;padding-bottom:16px;border-bottom:2px solid var(--rule);margin-left:62px;position:relative;min-height:58px}
  .contact:last-child{border-bottom:none}
  .contact__icon{position:absolute;left:-68px;top:50%;transform:translateY(-58%);width:46px;height:46px}
  .contact__text{font-size:17px;color:var(--ink);line-height:1.35}

  .name-band{height:148px;flex:none;background:var(--coral);display:flex;flex-direction:column;align-items:center;justify-content:center}
  .name-band__name{font-size:28px;font-weight:700;color:var(--navy);letter-spacing:.5px}
  .name-band__role{font-size:24px;color:var(--navy);margin-top:2px}
</style>
</head>
<body>

<section class="card card--front" aria-label="Card front">
  <div class="panel">
    <div class="top-band">
      <ul class="services">
        <li class="services__item">Mowing</li>
        <li class="services__item">Fertilization</li>
        <li class="services__item">Aeration</li>
        <li class="services__item services__item--break" aria-hidden="true"></li>
        <li class="services__item">Bed &amp; tree maintenance</li>
        <li class="services__item">and more</li>
      </ul>
    </div>
    <div class="divider"></div>
    <div class="brand">
      <span class="brand__dot"></span>
      <span class="brand__name">Greenstripe<br>Yard</span>
    </div>
  </div>
</section>

<section class="card card--back" aria-label="Card back">
  <div class="panel">
    <div class="top-band"></div>
    <div class="contacts">
      <div class="contact">
        <svg class="contact__icon" viewBox="0 0 46 46" aria-hidden="true">
          <circle cx="23" cy="23" r="20" fill="none" stroke="var(--navy)" stroke-width="3"/>
          <path d="M17 13c2 0 3 4 3 5s-2 2-2 3c1 3 3 5 6 7 1 0 2-2 3-2s5 1 5 3-2 4-4 4c-8-1-15-8-15-16 0-2 2-4 4-4z" fill="var(--navy)"/>
        </svg>
        <span class="contact__text">816-555-0147</span>
      </div>
      <div class="contact">
        <svg class="contact__icon" viewBox="0 0 46 46" aria-hidden="true">
          <circle cx="23" cy="23" r="20" fill="var(--navy)"/>
          <rect x="12" y="15" width="22" height="16" fill="#fff"/>
          <path d="M12 15l11 9 11-9" fill="none" stroke="var(--navy)" stroke-width="2"/>
        </svg>
        <span class="contact__text">greenstripeyard@fernmail.test</span>
      </div>
      <div class="contact">
        <svg class="contact__icon" viewBox="0 0 46 46" aria-hidden="true">
          <circle cx="23" cy="23" r="20" fill="var(--navy)"/>
          <path d="M23 11a8 8 0 0 1 8 8c0 6-8 16-8 16s-8-10-8-16a8 8 0 0 1 8-8z" fill="#fff"/>
          <circle cx="23" cy="19" r="3" fill="var(--navy)"/>
        </svg>
        <span class="contact__text">Unit 12, 48 Elm Row, KC 64105<br>1420 Maple Street NW</span>
      </div>
    </div>
    <div class="name-band">
      <span class="name-band__name">CARL WHITBY</span>
      <span class="name-band__role">Founder</span>
    </div>
  </div>
</section>

</body>
</html>
```